Wine Bottle Label for Corra Winslow California Wine

This will be a wine bottle label. The wine is produced from grapes from our family farm. Images at bottom are some of same ones in high resolution

Corra Winslow
Reserve Pinot Noir
Clarksburg 2023
Estate Grown (in cursive)

We would like to have a view from above, looking down from the levee there is a slough (wing of a river) running behind it, it looks down over vineyards, a big wood barn, a giant Oak Tree beyond the barn. There are beautiful sunsets there in the distance. Many birds fly over the vineyards including small black birds (as shown in one photo). Please use what you can from these suggestions to make a label. We will need a small image for back label and wording on it.

Other font styles liked:
• Wine bottle fonts

Requirements
Must have
• Wording mentioned . An Oak Tree with images of the vines and a sunset
Nice to have
• Flock of black birds flying in the sky

```html
<!DOCTYPE html>
<html lang="en">
<head>
<meta charset="UTF-8">
<title>Corra Winslow – Reserve Pinot Noir Label</title>
<link rel="stylesheet" href="https://fonts.googleapis.com/css2?family=Pinyon+Script&family=Cinzel:wght@400;500&family=Yellowtail&display=swap">
<style>
  :root {
    --paper: #f4f2ee;
    --paper-edge: #ebe8e2;
    --ink: #1c1c1c;
    --ink-soft: #3a3a3a;
    --gold: #c9a227;
    --gold-light: #e8cf6a;
    --gold-deep: #a9821a;
    --scene-light: #d9d9d7;
    --scene-mid: #a3a3a1;
    --scene-dark: #5c5c5a;
  }
  * { margin: 0; padding: 0; box-sizing: border-box; }
  html, body {
    width: 804px;
    height: 1200px;
    overflow: hidden;
    background: var(--paper);
  }
  .label {
    position: relative;
    width: 804px;
    height: 1200px;
    background: radial-gradient(ellipse at 50% 40%, var(--paper) 60%, var(--paper-edge) 100%);
  }
  .label__rule {
    position: absolute;
    top: 86px;
    height: 3px;
    background: var(--ink);
  }
  .label__rule--left { left: 34px; width: 308px; }
  .label__rule--right { left: 472px; width: 302px; }
  .label__seal {
    position: absolute;
    left: 362px;
    top: 26px;
    width: 84px;
    height: 120px;
  }
  .label__name {
    position: absolute;
    top: 232px;
    left: 0;
    width: 100%;
    text-align: center;
    font-family: "Pinyon Script", cursive;
    font-weight: 400;
    font-size: 100px;
    line-height: 1;
    color: var(--gold);
  }
  .label__variety {
    position: absolute;
    top: 430px;
    left: 0;
    width: 100%;
    text-align: center;
    font-family: "Cinzel", serif;
    font-size: 34px;
    letter-spacing: 4px;
    color: var(--ink-soft);
  }
  .label__estate {
    position: absolute;
    top: 486px;
    left: 0;
    width: 100%;
    text-align: center;
    font-family: "Yellowtail", cursive;
    font-size: 44px;
    line-height: 1.2;
    color: var(--ink);
  }
  .label__scene {
    position: absolute;
    left: 72px;
    top: 589px;
    width: 675px;
    height: 459px;
  }
  .label__appellation {
    position: absolute;
    top: 1076px;
    left: 0;
    width: 100%;
    text-align: center;
    font-family: "Cinzel", serif;
    font-size: 29px;
    letter-spacing: 5px;
    color: var(--ink);
  }
  .label__band {
    position: absolute;
    left: 0;
    top: 1148px;
    width: 100%;
    height: 28px;
    background: linear-gradient(90deg, var(--gold-deep) 0%, var(--gold-light) 35%, var(--gold) 65%, var(--gold-deep) 100%);
  }
</style>
</head>
<body>
  <main class="label">
    <div class="label__rule label__rule--left"></div>
    <div class="label__rule label__rule--right"></div>

    <svg class="label__seal" viewBox="0 0 84 120" aria-hidden="true">
      <ellipse cx="42" cy="60" rx="39" ry="56" fill="none" stroke="var(--gold)" stroke-width="4"/>
      <ellipse cx="42" cy="60" rx="29" ry="44" fill="var(--gold)" opacity="0.85"/>
    </svg>

    <h1 class="label__name">Corra Winslow</h1>
    <p class="label__variety">Reserve Pinot Noir</p>
    <p class="label__estate">Estate Grown</p>

    <svg class="label__scene" viewBox="0 0 665 451" preserveAspectRatio="none" role="img"
         aria-label="Black and white vineyard scene: rows of vines between two wooden barns, an oak tree at the horizon, a flock of birds in the sky">
      <defs>
        <linearGradient id="sceneTone" x1="0" y1="0" x2="0" y2="1">
          <stop offset="0" stop-color="var(--scene-light)"/>
          <stop offset="0.45" stop-color="var(--scene-mid)"/>
          <stop offset="1" stop-color="var(--scene-dark)"/>
        </linearGradient>
      </defs>
      <path d="M40 40 L160 28 L300 18 L470 30 L620 38 L650 110 L642 240 L655 300 L600 340 L540 360 L420 400 L300 425 L200 440 L130 405 L70 360 L30 290 L12 200 L20 110 Z"
            fill="url(#sceneTone)"/>
    </svg>

    <p class="label__appellation">Clarksburg 2023</p>
    <div class="label__band"></div>
  </main>
</body>
</html>
```